Awesome photographers card for an awesome new business

Double sided business card Black background and silver logo in middle on one side. Details on otherside. please keep it simple

Industry/Entity Type

Photographer

Contact Information for Business Card

Gerald Fenwick
0452817360
GeraldFenwickPhotography47@mailbox.test
www.GeraldFenwickPhotography.test.au
Instagram _Gerald_fenwick

Requirements
Must have
• My logo in Silver
• please use instagram logo instead of "Instagram"

```html
<!DOCTYPE html>
<html lang="en">
<head>
<meta charset="utf-8">
<title>Gerald Fenwick Photography – Business Card</title>
<link rel="stylesheet" href="https://fonts.googleapis.com/css2?family=Montserrat:wght@600&family=Questrial&display=swap">
<style>
  :root {
    --backdrop: #cfcfcf;
    --card-dark: #1a1a1c;
    --silver-deep: #5e5e60;
    --silver-mid: #8f8f91;
    --silver-light: #b9b9bb;
    --pearl: #f1f1f1;
    --ink-light: #ffffff;
    --logo-silver: #c9c9cb;
  }
  * { margin: 0; padding: 0; box-sizing: border-box; }
  html, body {
    width: 1200px; height: 960px; overflow: hidden;
    background: var(--backdrop);
  }
  .canvas { position: relative; width: 1200px; height: 960px; }

  .card {
    position: absolute; width: 600px; height: 342px;
    border-radius: 16px; overflow: hidden;
  }
  .card--front {
    left: 322px; top: 126px;
    background: linear-gradient(180deg, var(--silver-deep) 0%, var(--silver-light) 28%, var(--silver-mid) 70%, var(--silver-deep) 100%);
  }
  .card--back { left: 320px; top: 501px; background: var(--card-dark); }

  .front-art { position: absolute; inset: 0; }

  .contact {
    position: absolute; left: 22px; top: 216px;
    color: var(--ink-light);
    font-family: "Questrial", sans-serif;
  }
  .contact__name {
    font-family: "Montserrat", sans-serif; font-weight: 600;
    font-size: 19px; letter-spacing: 0.2px; margin-bottom: 8px;
  }
  .contact__list { list-style: none; }
  .contact__item {
    display: flex; align-items: center; gap: 8px;
    font-size: 11.5px; letter-spacing: -0.1px; line-height: 18px;
    white-space: nowrap;
  }
  .contact__icon { width: 12px; height: 12px; flex: none; }

  .brand-seal {
    position: absolute; left: 200px; top: 72px;
    width: 200px; height: 200px;
    display: flex; flex-direction: column; align-items: center; justify-content: center;
    border: 3px solid var(--logo-silver); border-radius: 50%;
    color: var(--logo-silver);
    font-family: "Questrial", sans-serif; text-align: center;
    font-size: 17px; letter-spacing: 3px; line-height: 26px;
  }
</style>
</head>
<body>
<main class="canvas">

  <section class="card card--front" aria-label="Business card front">
    <svg class="front-art" width="600" height="342" viewBox="0 0 600 342">
      <path d="M427 0 H600 V342 H427 Z" fill="var(--pearl)"/>
      <circle cx="427" cy="171" r="164" fill="var(--pearl)"/>
      <defs>
        <linearGradient id="apertureTone" x1="0" y1="0" x2="1" y2="1">
          <stop offset="0" stop-color="#6c6c6e"/>
          <stop offset="0.5" stop-color="#a9a9ab"/>
          <stop offset="1" stop-color="#6a6a6c"/>
        </linearGradient>
      </defs>
      <circle cx="427" cy="171" r="148" fill="url(#apertureTone)" role="img" aria-label="Camera aperture illustration"/>
    </svg>

    <div class="contact">
      <h1 class="contact__name">GERALD FENWICK</h1>
      <ul class="contact__list">
        <li class="contact__item">
          <svg class="contact__icon" viewBox="0 0 24 24"><path fill="#fff" d="M6.6 10.8a15 15 0 0 0 6.6 6.6l2.2-2.2c.3-.3.7-.4 1-.2 1.1.4 2.3.6 3.6.6.6 0 1 .4 1 1V20c0 .6-.4 1-1 1C10.6 21 3 13.4 3 4c0-.6.4-1 1-1h3.5c.6 0 1 .4 1 1 0 1.3.2 2.5.6 3.6.1.3 0 .7-.2 1z"/></svg>
          0452817360
        </li>
        <li class="contact__item">
          <svg class="contact__icon" viewBox="0 0 24 24"><path fill="#fff" d="M2 5h20v14H2z"/><path fill="none" stroke="#7a7a7c" stroke-width="2" d="M2 5l10 8 10-8"/></svg>
          GeraldFenwickPhotography47@mailbox.test
        </li>
        <li class="contact__item">
          <svg class="contact__icon" viewBox="0 0 24 24"><circle cx="12" cy="12" r="10" fill="none" stroke="#fff" stroke-width="2.4"/><path fill="none" stroke="#fff" stroke-width="2" d="M2 12h20M12 2c3 3 3 17 0 20M12 2c-3 3-3 17 0 20"/></svg>
          www.GeraldFenwickPhotography.test.au
        </li>
        <li class="contact__item">
          <svg class="contact__icon" viewBox="0 0 24 24"><rect x="3" y="3" width="18" height="18" fill="#fff"/></svg>
          Gerald_fenwick
        </li>
      </ul>
    </div>
  </section>

  <section class="card card--back" aria-label="Business card back">
    <div class="brand-seal">GERALD<br>FENWICK<br>PHOTOGRAPHY</div>
  </section>

</main>
</body>
</html>
```